Create a Dynamic Website for Roadhaven 41Ter!

Dear designers,
We have an exciting design opportunity for you on PixelBazaar. We are in need of a creative and professional website design for our company, Roadhaven 41Ter. Our current website is outdated and fails to convey the image we want to project. We are determined to revamp our online presence and create a website that truly represents who we are.
Roadhaven 41Ter is a versatile establishment offering a Velko Express, sandwich bar, restaurant, parking facilities, and meeting rooms. Each of these aspects deserves its own spotlight on our website. Therefore, we are seeking a WordPress-based website design that allows us to easily make changes, modify texts, and add new content as needed.
It is crucial that the design aligns seamlessly with our new branding and style. We invite you to explore our Instagram (@Roadhaven41ter) and Facebook (@Roadhaven) pages to gain an understanding of our branding and incorporate those elements into the design.
You can find our current website at www.guardedroadhaven.eu, but we want a new website that is vibrant, dynamic, and includes moving elements if possible. We believe this will enhance the user experience and keep visitors engaged for longer periods.
Key elements we would like to include in the new website design are as follows:
Clear presentation of all our services: Velko Express, sandwich bar, restaurant, parking facilities, and meeting rooms.
Easy navigation for visitors to find information effortlessly.
Engaging call-to-action buttons that encourage visitors to take specific actions, such as reserving a meeting room or placing an order.
A dedicated blog section where we can share news, events, and special offers.
Integration of a contact form and contact details for easy communication with our visitors.
Responsive design that works seamlessly across desktop and mobile devices.
We envision a modern and visually appealing website that leaves a lasting positive impression on visitors. We are interested in a design that incorporates creative visual elements and provides a user-friendly interface.
Thank you for your time, and we eagerly await your designs.
Best regards,

```html
<!DOCTYPE html>
<html lang="en">
<head>
<meta charset="utf-8">
<title>Services – Roadhaven 41Ter</title>
<link href="https://fonts.googleapis.com/css2?family=Poppins:wght@400;500;600;700&display=swap" rel="stylesheet">
<style>
:root{
  --blue:#1679c4;
  --blue-bright:#0f86d3;
  --navy:#232f7c;
  --ink:#2d2d2d;
  --muted:#7d7d7d;
  --line:#ececec;
  --white:#ffffff;
}
*{box-sizing:border-box;margin:0;padding:0}
html,body{width:1200px;height:5338px;overflow:hidden}
body{font-family:"Poppins",sans-serif;background:var(--white);color:var(--ink);position:relative}

.hero{position:absolute;left:0;top:0;width:1200px;height:440px;
  background:linear-gradient(180deg,#3a4a93 0%,#2a3680 55%,#1f2a6f 100%)}
.nav{position:absolute;left:91px;top:21px;width:1018px;height:58px;background:var(--white);
  display:flex;align-items:center;padding:0 28px}
.brand{display:flex;align-items:center;gap:8px;font-weight:700;font-size:15px;color:var(--navy);letter-spacing:.3px;white-space:nowrap}
.brand-mark{width:12px;height:12px;background:var(--blue)}
.nav-links{display:flex;height:58px;margin-left:166px;list-style:none}
.nav-links li{display:flex;align-items:center;padding:0 20px;font-size:11px;color:var(--ink)}
.nav-links li.active{background:var(--blue-bright);color:var(--white);font-weight:500}
.nav-call{margin-left:auto;font-size:11px;color:var(--ink);white-space:nowrap}
.nav-call b{font-weight:600}
.hero-title{position:absolute;left:0;right:0;top:240px;text-align:center;color:var(--white);font-size:56px;font-weight:600}

.eyebrow{position:absolute;left:0;right:0;top:528px;text-align:center;font-size:12px;color:var(--ink)}
.intro-title{position:absolute;left:0;right:0;top:562px;text-align:center;font-size:28px;font-weight:600;color:var(--blue)}

.card{position:absolute;border:1px solid var(--line);background:var(--white);text-align:center;
  display:flex;flex-direction:column;align-items:center;padding:0 40px}
.card.raised{box-shadow:0 4px 14px rgba(0,0,0,.08)}
.card-icon{height:60px;display:flex;align-items:flex-end;justify-content:center;margin-bottom:16px}
.card-title{font-size:14px;font-weight:600;color:var(--blue);text-transform:uppercase;margin-bottom:14px}
.card-text{font-size:11.5px;line-height:21px;color:var(--muted)}
.store-name{display:flex;align-items:center;gap:7px;font-size:14px;font-weight:600;color:var(--blue);padding-bottom:8px}
.store-name i{width:10px;height:10px;background:var(--blue);display:block}

.feature{position:absolute;left:97px;width:1006px;height:564px}
.media-main{position:absolute;top:0;width:487px;height:411px}
.media-thumbs{position:absolute;top:429px;width:487px;height:135px;display:flex;gap:1px}
.media-thumbs span{flex:1}
.media-right .media-main,.media-right .media-thumbs{left:519px}
.media-left .media-main,.media-left .media-thumbs{left:0}
.thumb-arrow{position:absolute;right:10px;top:58px;width:18px;height:18px}
.feature-copy{position:absolute;top:0;height:564px;width:430px;display:flex;flex-direction:column;justify-content:center}
.media-right .feature-copy{left:0}
.media-left .feature-copy{left:583px}
.feature-title{font-size:28px;font-weight:700;color:var(--blue);margin-bottom:14px}
.feature-text{font-size:12px;line-height:21px;color:var(--muted);margin-bottom:40px}
.ticks{list-style:none}
.ticks li{display:flex;align-items:center;gap:14px;height:35px;font-size:12.5px;font-weight:600;color:var(--blue)}
.ticks li span{color:var(--ink)}
.tick{width:14px;height:14px;flex:none}

.why{position:absolute;left:0;top:4766px;width:1200px;height:572px;background:var(--navy)}
.why-copy{position:absolute;left:97px;top:120px;width:410px;color:var(--white)}
.why-title{font-size:28px;font-weight:700;margin-bottom:16px}
.why-text{font-size:12px;line-height:21px}
.why-grid{position:absolute;left:112px;top:380px;display:grid;grid-template-columns:195px 150px;row-gap:12px;color:var(--white)}
.why-grid li{list-style:none;display:flex;align-items:center;gap:12px;font-size:13px;font-weight:600;line-height:22px}
.why-grid li span{max-width:110px}
.why-media{position:absolute;left:622px;top:85px;width:481px;height:487px;
  background:linear-gradient(160deg,#8a8f93 0%,#5f6870 50%,#747b73 100%)}
</style>
</head>
<body>

<svg width="0" height="0" style="position:absolute">
  <defs>
    <symbol id="tick" viewBox="0 0 14 14">
      <circle cx="7" cy="7" r="6" fill="none" stroke="currentColor" stroke-width="1.3"/>
      <path d="M4.2 7.2l2 2 3.8-4" fill="none" stroke="currentColor" stroke-width="1.3"/>
    </symbol>
    <symbol id="chev" viewBox="0 0 18 18">
      <path d="M7 4l5 5-5 5" fill="none" stroke="#fff" stroke-width="2"/>
    </symbol>
  </defs>
</svg>

<header class="hero" role="img" aria-label="Roadside service station building behind a dark blue overlay">
  <nav class="nav">
    <div class="brand"><span class="brand-mark"></span>ROADHAVEN 41TER</div>
    <ul class="nav-links">
      <li>Home</li><li class="active">Services</li><li>About</li><li>Blog</li><li>Contact</li>
    </ul>
    <div class="nav-call">Call us: <b>(123) 4567 890</b></div>
  </nav>
  <h1 class="hero-title">Services</h1>
</header>

<p class="eyebrow">Our Services</p>
<h2 class="intro-title">We provide the best services</h2>

<div class="card" style="left:97px;top:659px;width:320px;height:348px;padding-top:62px">
  <div class="card-icon"><span class="store-name"><i></i>Velko Express</span></div>
  <h3 class="card-title">Velko Express</h3>
  <p class="card-text">Fuel up on the go with our well-stocked Velko Express convenience store.</p>
</div>
<div class="card" style="left:441px;top:659px;width:320px;height:348px;padding-top:50px">
  <div class="card-icon">
    <svg width="72" height="40" viewBox="0 0 72 40"><path d="M4 30L36 4l32 26z" fill="none" stroke="var(--blue)" stroke-width="3"/><rect x="4" y="30" width="64" height="7" rx="2" fill="var(--blue)"/><path d="M14 26h44" stroke="var(--blue)" stroke-width="2" stroke-dasharray="4 3"/></svg>
  </div>
  <h3 class="card-title">Sandwich Bar</h3>
  <p class="card-text">Treat your taste buds to an array of delectable sandwiches made with fresh ingredients.</p>
</div>
<div class="card" style="left:784px;top:659px;width:319px;height:348px;padding-top:50px">
  <div class="card-icon">
    <svg width="80" height="60" viewBox="0 0 80 60"><circle cx="40" cy="30" r="22" fill="none" stroke="var(--blue)" stroke-width="3"/><circle cx="40" cy="30" r="15" fill="var(--blue)"/><path d="M8 6v48M4 6v14q4 4 8 0V6" fill="none" stroke="var(--blue)" stroke-width="3"/><path d="M72 6v48M72 6q-6 8 0 20" fill="none" stroke="var(--blue)" stroke-width="3"/></svg>
  </div>
  <h3 class="card-title">Restaurant</h3>
  <p class="card-text">Indulge in a culinary adventure at our restaurant, where exquisite dishes meet a warm and welcoming ambiance.</p>
</div>
<div class="card raised" style="left:91px;top:1032px;width:496px;height:293px;padding:44px 80px 0">
  <div class="card-icon">
    <svg width="56" height="60" viewBox="0 0 56 60"><path d="M28 2a11 11 0 0111 11c0 8-11 17-11 17S17 21 17 13A11 11 0 0128 2z" fill="none" stroke="var(--blue)" stroke-width="3"/><circle cx="28" cy="13" r="4" fill="var(--blue)"/><path d="M8 44l6-10h28l6 10v12H8z" fill="var(--blue)"/><circle cx="16" cy="48" r="3" fill="#fff"/><circle cx="40" cy="48" r="3" fill="#fff"/></svg>
  </div>
  <h3 class="card-title">Parking Facilities</h3>
  <p class="card-text">Rest easy knowing that we provide ample and secure parking spaces for your vehicles.</p>
</div>
<div class="card raised" style="left:612px;top:1032px;width:497px;height:293px;padding:44px 80px 0">
  <div class="card-icon">
    <svg width="70" height="60" viewBox="0 0 70 60"><rect x="27" y="4" width="16" height="10" fill="none" stroke="var(--blue)" stroke-width="2"/><circle cx="35" cy="22" r="5" fill="var(--blue)"/><rect x="20" y="30" width="30" height="5" fill="var(--blue)"/><circle cx="14" cy="42" r="5" fill="var(--blue)"/><circle cx="35" cy="42" r="5" fill="var(--blue)"/><circle cx="56" cy="42" r="5" fill="var(--blue)"/><path d="M6 58q8-12 16 0M27 58q8-12 16 0M48 58q8-12 16 0" fill="var(--blue)"/></svg>
  </div>
  <h3 class="card-title">Meeting Rooms</h3>
  <p class="card-text">Need a professional space to host your next business gathering? Look no further.</p>
</div>

<section class="feature media-right" style="top:1397px">
  <div class="feature-copy">
    <h2 class="feature-title">Velko Express</h2>
    <p class="feature-text">Fuel up on the go with our well-stocked Velko Express convenience store. From snacks and beverages to everyday essentials, we provide everything you need for your journey. Browse our aisles and find the perfect items to keep you going.</p>
    <ul class="ticks">
      <li><svg class="tick"><use href="#tick"/></svg><span>Well-stocked convenience store</span></li>
      <li><svg class="tick"><use href="#tick"/></svg><span>Quick and convenient stop for travelers</span></li>
      <li><svg class="tick"><use href="#tick"/></svg><span>Find everything you need in one place</span></li>
      <li><svg class="tick"><use href="#tick"/></svg><span>Quality products and friendly service</span></li>
    </ul>
  </div>
  <div class="media-main" role="img" aria-label="Cashier serving at the convenience store counter" style="background:linear-gradient(135deg,#3a3d44 0%,#5b5f66 55%,#2b2e35 100%)"></div>
  <div class="media-thumbs">
    <span role="img" aria-label="Shopper in the store aisles" style="background:linear-gradient(135deg,#8c8f93,#5a5f66)"></span>
    <span role="img" aria-label="Well-stocked shelves" style="background:linear-gradient(135deg,#9b5a5a,#6f6a70)"></span>
    <span role="img" aria-label="Store entrance" style="background:linear-gradient(135deg,#b7b2ac,#6c6f72)"></span>
    <svg class="thumb-arrow"><use href="#chev"/></svg>
  </div>
</section>

<section class="feature media-left" style="top:2075px">
  <div class="media-main" role="img" aria-label="Hands placing a fresh baguette sandwich on a tray" style="background:linear-gradient(160deg,#3a3b3c 0%,#8a5a33 45%,#1f7f7f 100%)"></div>
  <div class="media-thumbs">
    <span role="img" aria-label="Burger and fries" style="background:linear-gradient(135deg,#c9a06a,#3f6f7a)"></span>
    <span role="img" aria-label="Stacked burgers" style="background:linear-gradient(135deg,#d08a3d,#4f6a73)"></span>
    <span role="img" aria-label="Fried snacks on a plate" style="background:linear-gradient(135deg,#c99048,#2f6b78)"></span>
  </div>
  <div class="feature-copy">
    <h2 class="feature-title">Sandwich Bar</h2>
    <p class="feature-text">Treat your taste buds to an array of delectable sandwiches made with fresh ingredients. Our talented chefs have crafted a menu that caters to diverse palates. Experience the perfect combination of flavors and textures, lovingly prepared to satisfy your cravings.</p>
    <ul class="ticks">
      <li><svg class="tick"><use href="#tick"/></svg><span>Delicious sandwiches</span></li>
      <li><svg class="tick"><use href="#tick"/></svg><span>Made with fresh, high-quality ingredients</span></li>
      <li><svg class="tick"><use href="#tick"/></svg><span>Variety of flavors to suit every palate.</span></li>
      <li><svg class="tick"><use href="#tick"/></svg><span>Tasty meal on the go</span></li>
    </ul>
  </div>
</section>

<section class="feature media-right" style="top:2753px">
  <div class="feature-copy">
    <h2 class="feature-title">Restaurant</h2>
    <p class="feature-text">Indulge in a culinary adventure at our restaurant, where exquisite dishes meet a warm and welcoming ambiance. From hearty breakfast options to delightful dinner choices, our menu showcases the finest ingredients, expertly prepared to tantalize your senses.</p>
    <ul class="ticks">
      <li><svg class="tick"><use href="#tick"/></svg><span>Culinary delights with a diverse menu</span></li>
      <li><svg class="tick"><use href="#tick"/></svg><span>Fresh, locally sourced ingredients</span></li>
      <li><svg class="tick"><use href="#tick"/></svg><span>Warm and inviting ambiance</span></li>
      <li><svg class="tick"><use href="#tick"/></svg><span>Attentive staff providing excellent service</span></li>
    </ul>
  </div>
  <div class="media-main" role="img" aria-label="Guests dining at tables under a festive tent" style="background:linear-gradient(170deg,#d9d3c8 0%,#a08a70 50%,#4d3a2c 100%)"></div>
  <div class="media-thumbs">
    <span role="img" aria-label="Outdoor tent terrace" style="background:linear-gradient(135deg,#c9d3dc,#8a7a5a)"></span>
    <span role="img" aria-label="Guests at the restaurant" style="background:linear-gradient(135deg,#6a7480,#3a4a5a)"></span>
    <span role="img" aria-label="Pasta dish" style="background:linear-gradient(135deg,#d49a4a,#3f6a70)"></span>
    <svg class="thumb-arrow"><use href="#chev"/></svg>
  </div>
</section>

<section class="feature media-left" style="top:3429px">
  <div class="media-main" role="img" aria-label="Electric car at charging stations under a red canopy" style="background:linear-gradient(180deg,#9a2c2c 0%,#b7bcc0 30%,#8f9498 70%,#77797a 100%)"></div>
  <div class="media-thumbs">
    <span role="img" aria-label="Aerial view of parking grounds" style="background:linear-gradient(135deg,#7a8580,#4d5552)"></span>
    <span role="img" aria-label="Aerial view of truck parking" style="background:linear-gradient(135deg,#6c7278,#3e4448)"></span>
    <span role="img" aria-label="Aerial view of the site" style="background:linear-gradient(135deg,#7d8a7a,#505a55)"></span>
  </div>
  <div class="feature-copy">
    <h2 class="feature-title">Parking Facilities</h2>
    <p class="feature-text">Rest easy knowing that we provide ample and secure parking spaces for your vehicles. Our spacious parking facilities offer convenience and peace of mind, making Roadhaven 41Ter the ideal pit stop for travelers and truckers alike.</p>
    <ul class="ticks">
      <li><svg class="tick"><use href="#tick"/></svg><span>Secure parking spaces</span></li>
      <li><svg class="tick"><use href="#tick"/></svg><span>Spacious and safe environment</span></li>
      <li><svg class="tick"><use href="#tick"/></svg><span>Location for short or long-term parking</span></li>
      <li><svg class="tick"><use href="#tick"/></svg><span>Well-maintained facilitie</span></li>
    </ul>
  </div>
</section>

<section class="feature media-right" style="top:4107px">
  <div class="feature-copy">
    <h2 class="feature-title">Meeting Rooms</h2>
    <p class="feature-text">Need a professional space to host your next business gathering? Look no further. Our versatile meeting rooms are equipped with modern amenities and can be customized to suit your specific requirements. Conduct meetings, seminars, or workshops in an environment designed to foster productivity and collaboration.</p>
    <ul class="ticks">
      <li><svg class="tick"><use href="#tick"/></svg><span>Versatile meeting spaces</span></li>
      <li><svg class="tick"><use href="#tick"/></svg><span>Equipped with modern amenities</span></li>
      <li><svg class="tick"><use href="#tick"/></svg><span>Customizable setups</span></li>
      <li><svg class="tick"><use href="#tick"/></svg><span>Professional atmosphere to enhance collaboration</span></li>
    </ul>
  </div>
  <div class="media-main" role="img" aria-label="People seated around a bright meeting room table" style="background:linear-gradient(160deg,#e6e6e4 0%,#c8c8c6 50%,#6a6a6a 100%)"></div>
  <div class="media-thumbs">
    <span role="img" aria-label="Meeting in progress" style="background:linear-gradient(135deg,#dcdcda,#8a8a8a)"></span>
    <span role="img" aria-label="Empty meeting room with tables" style="background:linear-gradient(135deg,#eaeae8,#9a9a98)"></span>
    <span role="img" aria-label="Meeting room layout" style="background:linear-gradient(135deg,#e2e2e0,#a09f9c)"></span>
    <svg class="thumb-arrow"><use href="#chev"/></svg>
  </div>
</section>

<section class="why">
  <div class="why-copy">
    <h2 class="why-title">Why choose us?</h2>
    <p class="why-text">Choose Roadhaven 41Ter as your preferred destination, and experience the difference we offer. Whether it's for a quick pit stop, a satisfying meal, a secure parking space, or a productive business meeting, we are dedicated to providing you with the best service, quality, and convenience. Join us and discover why we are the preferred choice for those seeking a versatile and delightful experience.</p>
  </div>
  <ul class="why-grid">
    <li><svg class="tick"><use href="#tick"/></svg><span>Versatile services</span></li>
    <li><svg class="tick"><use href="#tick"/></svg><span>Exceptional Service</span></li>
    <li><svg class="tick"><use href="#tick"/></svg><span>Quality &amp; Freshness</span></li>
    <li><svg class="tick"><use href="#tick"/></svg><span>Engaging Atmosphere</span></li>
    <li><svg class="tick"><use href="#tick"/></svg><span>Convenient Location</span></li>
    <li><svg class="tick"><use href="#tick"/></svg><span>Commitment to Community</span></li>
  </ul>
  <div class="why-media" role="img" aria-label="Aerial view of the service area, parking lots and surrounding roads"></div>
</section>

</body>
</html>
```